Kelvaro.ch is looking for business card letterhead and envelope C5 with WOW effect

We need a strong business card for our company Kelvaro.ch, logo is available. You want a black or dark background on which the logo Stark r% 26 # 252; appears. Letterhead and envelope in C5 format should be in a similar design, but does not have to be We need a strong business card for our company Kelvaro.ch, logo is available. A black or dark background is desired, on which the logo Stark comes across. The letterhead and the envelope in C5 format should have a similar design.

Target Market(s)

Private customers as well as entrepreneurs

Contact Information for Business Card

E-mail: info@kelvaro-example.ch
Web.www.Kelvaro-example.ch
Tel: +41 ( 0 ) 79 482 6037
Adresse:
Lindenweg 14
9406 Tarnbach

Hier kann man Icons verwenden für Email,Tel und Adressse

Font styles to use
Other font styles liked:
• Dubai,bold

Colors

Designer to choose colors to be used in the design.

Requirements
Must have
• WOW effect
Nice to have
• R% 26 # 252; back business card with our service listings. - VEHICLE LABELING - SHOP WINDOW LABELING - STICKERS AND MUCH MORE ... in red color

```html
<!DOCTYPE html>
<html lang="en">
<head>
<meta charset="utf-8">
<title>Kelvaro.ch – Business Card</title>
<link rel="stylesheet" href="https://fonts.googleapis.com/css2?family=Archivo:wght@400;800&display=swap">
<style>
  :root {
    --backdrop: #2f2f2f;
    --card-white: #ffffff;
    --brand-yellow: #fdc91c;
    --yellow-deep: #efb70e;
    --service-red: #e8234f;
    --ink: #111111;
    --pattern-grey: #e9e9e9;
  }
  * { box-sizing: border-box; margin: 0; padding: 0; }
  html, body {
    width: 1200px; height: 866px; overflow: hidden;
    background: var(--backdrop);
    font-family: "Archivo", Arial, sans-serif;
  }
  .stage {
    width: 1200px; height: 866px;
    display: flex; align-items: center; justify-content: center; gap: 40px;
  }
  .card {
    position: relative;
    width: 540px; height: 350px;
    overflow: hidden;
    box-shadow: 0 10px 24px rgba(0,0,0,.45);
  }

  /* Front */
  .card--front { background: var(--card-white); }
  .card--front .base-band {
    position: absolute; left: 0; right: 0; bottom: 0; height: 12px;
    background: var(--brand-yellow);
  }
  .card--front .pattern-area {
    position: absolute; left: 0; top: 0; width: 240px; height: 338px;
    background: linear-gradient(100deg, var(--pattern-grey) 0%, #f3f3f3 55%, rgba(255,255,255,0) 100%);
  }
  .brand {
    position: absolute; left: 210px; top: 128px;
    display: flex; align-items: center; gap: 12px;
  }
  .brand__mark {
    width: 30px; height: 30px; background: var(--brand-yellow); flex: none;
  }
  .brand__name {
    font-weight: 800; font-size: 30px; letter-spacing: 1px; white-space: nowrap;
    color: var(--ink); text-transform: uppercase;
  }
  .contact {
    position: absolute; left: 34px; top: 192px;
    list-style: none; font-size: 14px; color: var(--ink);
  }
  .contact li { display: flex; align-items: center; gap: 8px; height: 22px; }
  .contact svg { width: 15px; height: 15px; flex: none; }
  .address {
    position: absolute; right: 30px; bottom: 34px;
    font-size: 14px; color: var(--ink);
  }

  /* Back */
  .card--back { background: var(--brand-yellow); }
  .card--back .pattern-area {
    position: absolute; left: 0; top: 0; width: 240px; height: 350px;
    background: linear-gradient(90deg, var(--yellow-deep) 0%, rgba(239,183,14,.5) 55%, rgba(239,183,14,0) 100%);
  }
  .services {
    position: absolute; left: 170px; top: 122px;
    list-style: none; font-weight: 800; font-size: 20px;
    color: var(--service-red); text-transform: uppercase; line-height: 34px;
    white-space: nowrap;
  }
</style>
</head>
<body>
<main class="stage">
  <section class="card card--front" aria-label="Business card front">
    <div class="pattern-area" role="img" aria-label="Faint grey hexagon pattern area"></div>
    <div class="brand">
      <span class="brand__mark"></span>
      <span class="brand__name">Kelvaro.ch</span>
    </div>
    <ul class="contact">
      <li>
        <svg viewBox="0 0 16 16"><rect x="1" y="1" width="14" height="14" rx="2" fill="none" stroke="#fdc91c" stroke-width="1.6"/><path d="M5 4l2 0 1 2.5-1.2 1a6 6 0 0 0 2.7 2.7l1-1.2L13 10v2c-5 .5-9-3.5-8-8z" fill="#fdc91c"/></svg>
        +41 ( 0 ) 79 482 6037
      </li>
      <li>
        <svg viewBox="0 0 16 16"><rect x="1" y="3" width="14" height="10" fill="#fdc91c"/><path d="M1 3l7 6 7-6" fill="none" stroke="#fff" stroke-width="1.2"/></svg>
        info@kelvaro-example.ch
      </li>
      <li>
        <svg viewBox="0 0 16 16"><circle cx="8" cy="8" r="7" fill="#fdc91c"/><path d="M1 8h14M8 1v14M3 4.5h10M3 11.5h10" stroke="#fff" stroke-width="1"/><ellipse cx="8" cy="8" rx="3.2" ry="7" fill="none" stroke="#fff" stroke-width="1"/></svg>
        www.Kelvaro-example.ch
      </li>
    </ul>
    <p class="address">Lindenweg 14, 9406 Tarnbach</p>
    <div class="base-band"></div>
  </section>

  <section class="card card--back" aria-label="Business card back">
    <div class="pattern-area" role="img" aria-label="Embossed hexagon pattern area in yellow"></div>
    <ul class="services">
      <li>Vehicle labeling</li>
      <li>Shop window labeling</li>
      <li>Stickers and much more ...</li>
    </ul>
  </section>
</main>
</body>
</html>
```